Building company buisness cards

We are looking for a sharp modern new look for our business cards.
We are a New Zealand based company that specialises in house and land packages.
We have attached a photo of the current logo and would like to see if it can be improved somehow if needed.
We are open to any colours but we have chosen green at this stage.
Feel free to change the font and make the logo smarter looking.
Play with the colours and see what looks best.

We want a card that looks so good know one will want to throw it away!

Target Market(s)

Home buyers

Industry/Entity Type

Building

Contact Information for Business Card

Derek Tolvane
0217394062
dtolvane@quillmarkhomesteads.co.nz
quillmarkhomesteads.co.nz

Font styles to use
Serif
Sans Serif

Colors

Designer to choose colors to be used in the design.

Requirements
Must have
• Logo and company name on one side, details on the other side
Nice to have
• Color codes for the original green are HEX #4a8028, RGB(74,128,40), CMYK(42,0,69,50)
• Round corners, Raised and/or spot UV

```html
<!DOCTYPE html>
<html lang="en">
<head>
<meta charset="utf-8">
<title>Quillmark Homesteads – Business Card</title>
<link rel="stylesheet" href="https://fonts.googleapis.com/css2?family=Open+Sans:wght@400;700&display=swap">
<style>
  :root {
    --backdrop: #2c2c2c;
    --brand-green: #1f8a1b;
    --card-white: #f4f4f4;
    --swoosh-black: #0d0d0d;
    --ink-dark: #151515;
    --ink-light: #ffffff;
  }
  html, body {
    margin: 0;
    padding: 0;
    width: 1200px;
    height: 923px;
    overflow: hidden;
    background: var(--backdrop);
  }
  .canvas {
    position: relative;
    width: 1200px;
    height: 923px;
  }
  .business-card {
    position: absolute;
    left: 100px;
    top: 176px;
    width: 1000px;
    height: 571px;
    border-radius: 14px;
    overflow: hidden;
    background: var(--brand-green);
    box-shadow: 0 18px 40px rgba(0,0,0,0.45);
    font-family: "Open Sans", Arial, sans-serif;
  }
  .card-shapes {
    position: absolute;
    inset: 0;
    width: 100%;
    height: 100%;
  }
  .company-name {
    position: absolute;
    left: 150px;
    top: 150px;
    width: 600px;
    margin: 0;
    text-align: center;
    color: var(--brand-green);
    font-size: 42px;
    font-weight: 700;
    line-height: 1.2;
  }
  .holder-name {
    position: absolute;
    right: 110px;
    top: 322px;
    margin: 0;
    font-size: 26px;
    font-weight: 400;
    color: var(--ink-dark);
  }
  .contact-list {
    position: absolute;
    left: 40px;
    bottom: 40px;
    margin: 0;
    padding: 0;
    list-style: none;
    color: var(--ink-light);
    font-size: 21px;
    line-height: 30px;
  }
  .contact-list li {
    display: flex;
    align-items: center;
    gap: 12px;
  }
  .contact-icon {
    width: 20px;
    height: 20px;
    flex: none;
  }
</style>
</head>
<body>
<main class="canvas">
  <section class="business-card" aria-label="Business card front">
    <svg class="card-shapes" viewBox="0 0 1000 571" preserveAspectRatio="none" aria-hidden="true">
      <path class="swoosh" fill="var(--swoosh-black)"
        d="M0,300 C120,350 260,378 400,378 C470,378 535,370 590,356 C525,384 465,398 400,400 C240,404 110,376 0,342 Z"/>
      <path class="white-field" fill="var(--card-white)"
        d="M0,0 H890 C830,240 630,366 400,366 C230,366 90,330 0,292 Z"/>
    </svg>

    <p class="company-name">Quillmark Homesteads</p>

    <p class="holder-name">Derek Tolvane</p>

    <ul class="contact-list">
      <li>
        <svg class="contact-icon" viewBox="0 0 20 20" aria-hidden="true">
          <circle cx="10" cy="10" r="10" fill="var(--swoosh-black)"/>
          <path d="M7 5.5 l1.6 2.2 -1 1 c.7 1.4 1.6 2.3 3 3 l1-1 2.2 1.6 -.9 1.6 c-3.6-.3-6.2-2.9-6.6-6.6 z" fill="var(--ink-light)"/>
        </svg>
        0217394062
      </li>
      <li>
        <svg class="contact-icon" viewBox="0 0 20 20" aria-hidden="true">
          <circle cx="10" cy="10" r="10" fill="var(--swoosh-black)"/>
          <rect x="5" y="6.5" width="10" height="7" fill="none" stroke="var(--ink-light)" stroke-width="1.2"/>
          <path d="M5 6.5 L10 10.5 L15 6.5" fill="none" stroke="var(--ink-light)" stroke-width="1.2"/>
        </svg>
        dtolvane@quillmarkhomesteads.co.nz
      </li>
      <li>
        <svg class="contact-icon" viewBox="0 0 20 20" aria-hidden="true">
          <circle cx="10" cy="10" r="10" fill="var(--swoosh-black)"/>
          <circle cx="10" cy="10" r="5" fill="none" stroke="var(--ink-light)" stroke-width="1.2"/>
          <ellipse cx="10" cy="10" rx="2.2" ry="5" fill="none" stroke="var(--ink-light)" stroke-width="1"/>
          <line x1="5" y1="10" x2="15" y2="10" stroke="var(--ink-light)" stroke-width="1"/>
        </svg>
        quillmarkhomesteads.co.nz
      </li>
    </ul>
  </section>
</main>
</body>
</html>
```